Business Card for a Creative Technology based HR services company

Our company name is Lumo8, and we build large communities of HR (human resource) and finance personnels through our mobile platform, and we conduct lots of on-line and off-line activities to get everyone constantly connected. Behind all these, we will also provide on-site HR and finance contractors to our clients, plus a host of other HR-related services. No process in our company takes more than 5-steps.
Our company slogan: Shaping What Comes Next
Target Market(s)
All human resource (HR) and finance personnels, from new entrants to highly experienced senior professionals.
Industry/Entity Type
Finance
Colors
Designer to choose colors to be used in the design.
Look and feel
Each slider illustrates characteristics of the customer's brand and the style your logo design should communicate.

```html
<!DOCTYPE html>
<html lang="en">
<head>
<meta charset="utf-8">
<title>Lumo8 Business Card</title>
<link rel="stylesheet" href="https://fonts.googleapis.com/css2?family=Cinzel:wght@400;700&family=Josefin+Sans:wght@300;400&display=swap">
<style>
  :root {
    --navy: #1b2d55;
    --red: #e4161b;
    --paper: #f4f4f3;
    --ink: #3a3a3a;
    --rule: #9a9a9a;
    --backdrop: #e3e1dd;
  }
  * { box-sizing: border-box; margin: 0; padding: 0; }
  html, body { width: 1200px; height: 900px; overflow: hidden; }
  body {
    background: var(--backdrop);
    font-family: "Josefin Sans", sans-serif;
    position: relative;
  }
  .card {
    position: absolute;
    left: 267px;
    width: 665px;
    height: 380px;
    background: var(--paper);
    box-shadow: 0 6px 18px rgba(0,0,0,0.14);
    overflow: hidden;
  }
  .card--front { top: 50px; }
  .card--back { top: 470px; }

  .brand {
    font-family: "Cinzel", serif;
    font-weight: 400;
    color: var(--ink);
    letter-spacing: 3px;
    line-height: 1;
  }
  .card--front .brand {
    position: absolute;
    top: 140px; left: 0; right: 0;
    text-align: center;
    font-size: 56px;
  }
  .slogan {
    position: absolute;
    top: 222px; left: 0; right: 0;
    text-align: center;
    font-family: "Cinzel", serif;
    font-size: 13px;
    letter-spacing: 4px;
    color: var(--navy);
    text-transform: uppercase;
  }

  .card--back .brand {
    position: absolute;
    top: 48px; left: 200px;
    font-size: 36px;
  }
  .divider {
    position: absolute;
    top: 108px; left: 140px; right: 40px;
    height: 1px;
    background: var(--rule);
  }
  .address {
    position: absolute;
    top: 128px; left: 40px;
    font-style: normal;
    font-size: 11px;
    letter-spacing: 2.5px;
    line-height: 20px;
    color: var(--ink);
    text-transform: uppercase;
  }
  .person {
    position: absolute;
    top: 142px; right: 40px;
    text-align: right;
  }
  .person__name {
    font-family: "Cinzel", serif;
    font-size: 20px;
    letter-spacing: 4px;
    color: var(--ink);
  }
  .person__title {
    font-family: "Cinzel", serif;
    font-size: 13px;
    letter-spacing: 3px;
    color: var(--navy);
    margin-top: 4px;
    padding-bottom: 8px;
    border-bottom: 1px solid var(--rule);
  }
  .contacts {
    list-style: none;
    position: absolute;
    top: 218px; right: 40px;
    font-size: 13px;
    letter-spacing: 1.5px;
    color: var(--ink);
  }
  .contacts li {
    display: flex;
    justify-content: flex-end;
    align-items: center;
    gap: 12px;
    height: 22px;
  }
  .contacts svg { width: 14px; height: 14px; flex: none; }
  .swoosh { position: absolute; left: 0; top: 0; }
</style>
</head>
<body>

<section class="card card--front" aria-label="Card front">
  <p class="brand">Lumo8</p>
  <p class="slogan">Shaping What Comes Next</p>
</section>

<section class="card card--back" aria-label="Card back">
  <svg class="swoosh" width="665" height="380" viewBox="0 0 665 380" aria-hidden="true">
    <path d="M0 210 C200 282 420 337 665 352 L665 380 L0 380 Z" fill="var(--red)"/>
    <path d="M0 190 C200 262 380 342 540 384" fill="none" stroke="var(--navy)" stroke-width="6"/>
  </svg>

  <p class="brand">Lumo8</p>
  <div class="divider"></div>

  <address class="address">
    418 Linden Ave. Suite #4<br>
    Fair Oaks, CA 95628
  </address>

  <div class="person">
    <p class="person__name">DANA WHITFIELD</p>
    <p class="person__title">CEO</p>
  </div>

  <ul class="contacts">
    <li>555-214-3087
      <svg viewBox="0 0 14 14" fill="none" stroke="var(--red)" stroke-width="1.5"><path d="M3 1.5 L5.5 1.5 L6.2 4.5 L4.6 5.6 C5.4 7.3 6.7 8.6 8.4 9.4 L9.5 7.8 L12.5 8.5 L12.5 11 C12.5 12 11.6 12.6 10.7 12.5 C5.6 11.9 2.1 8.4 1.5 3.3 C1.4 2.4 2 1.5 3 1.5 Z"/></svg>
    </li>
    <li>555-402-6615
      <svg viewBox="0 0 14 14" fill="none" stroke="var(--red)" stroke-width="1.5"><rect x="3.5" y="1" width="7" height="12" rx="1.2"/><line x1="6" y1="11" x2="8" y2="11"/></svg>
    </li>
    <li>555-739-1148
      <svg viewBox="0 0 14 14" fill="none" stroke="var(--red)" stroke-width="1.5"><rect x="1.5" y="5" width="11" height="6" rx="1"/><rect x="4" y="1.5" width="6" height="3.5"/><rect x="4" y="9" width="6" height="3.5"/></svg>
    </li>
    <li>dwhitfield@lumo8.com
      <svg viewBox="0 0 14 14" fill="none" stroke="var(--red)" stroke-width="1.5"><rect x="1" y="3" width="12" height="8.5"/><path d="M1 3 L7 8 L13 3"/></svg>
    </li>
  </ul>
</section>

</body>
</html>
```